Catering Menu Package

I currently have a complete menu package, which we have redesigned as far as content, now I need to it put together in a catalog type format. It is essentially 10-12 pages in length, and will be sent for print production. Upon receiving a final edit
Updates

I have added an example gif to the project.

I did this free hand this basically what I am looking for. please change text and type to whatever you think would look best. This is a total rough design so, feel free to change any and everything. The text for the page is on the word documents. If you need more images let me know I am in the process of getting as many images uploaded for your use.

Project Deadline Extended
Reason: I figured we got a late jump with questions, so i am extending a few days .

Target Market(s)

The target market is business who wish to have catered luncheons, breakfasts , meetings

Industry/Entity Type

Catering

Requirements
Must have
• I have attached a copy of the text that what we want in the package, our logo, and i have also attached a catering package of another company to give you an idea what the finished product will be
Should not have
• It should not look identical to the example catering packages, these are for some inspiration we want our own design with the same type of look and feel

```html
<!DOCTYPE html>
<html lang="en">
<head>
<meta charset="utf-8">
<title>Sandwiches &amp; Wraps – Harbor Valley Caterers</title>
<link href="https://fonts.googleapis.com/css2?family=Parisienne&family=Lora:ital,wght@0,400;1,700&family=Ropa+Sans&display=swap" rel="stylesheet">
<style>
  :root {
    --paper: #ffffff;
    --band-dark: #cfc6bf;
    --band-light: #f4f1ee;
    --ink: #2b1a10;
    --accent-brown: #8a4a1a;
    --accent-pink: #e0506a;
    --muted: #6b5a55;
    --script: #6e625c;
    --brand: #2b1a10;
    --brand-orange: #e2672a;
  }
  html, body { margin: 0; padding: 0; overflow: hidden; background: var(--paper); }
  .menu-page {
    position: relative;
    width: 1200px;
    height: 927px;
    overflow: hidden;
    background: linear-gradient(90deg, var(--band-dark) 0, var(--band-light) 182px, var(--paper) 420px);
    font-family: "Lora", Georgia, serif;
  }
  .brand {
    position: absolute;
    left: 28px;
    top: 110px;
    width: 135px;
    display: flex;
    flex-direction: column;
    align-items: flex-start;
    gap: 12px;
  }
  .brand-mark { width: 26px; height: 26px; background: var(--brand-orange); }
  .brand-name {
    font-family: "Lora", Georgia, serif;
    font-size: 21px;
    line-height: 26px;
    color: var(--brand);
  }
  .section-title {
    position: absolute;
    margin: 0;
    font-family: "Parisienne", cursive;
    font-weight: 400;
    line-height: 1.2;
    white-space: nowrap;
    color: var(--script);
    text-shadow: 1px 1px 2px rgba(0,0,0,0.18);
  }
  .section-title--classic { left: 195px; top: 54px; font-size: 36px; }
  .section-title--signature { left: 688px; top: 54px; font-size: 34px; }
  .classic-list {
    position: absolute;
    left: 197px;
    top: 124px;
    margin: 0; padding: 0;
    list-style: none;
    font-size: 16.5px;
    line-height: 24px;
    white-space: nowrap;
  }
  .classic-list li { margin-bottom: 24px; color: var(--ink); }
  .classic-list li:nth-child(even) { color: var(--accent-brown); }
  .classic-note {
    position: absolute;
    left: 197px;
    top: 720px;
    margin: 0;
    font-family: "Ropa Sans", Arial, sans-serif;
    font-size: 15px;
    line-height: 19px;
    white-space: nowrap;
    color: var(--ink);
  }
  .signature-list {
    position: absolute;
    left: 691px;
    top: 128px;
    margin: 0; padding: 0;
    list-style: none;
    white-space: nowrap;
  }
  .signature-item { margin-bottom: 22px; }
  .signature-name {
    margin: 0;
    font-style: italic;
    font-weight: 700;
    font-size: 18px;
    line-height: 26px;
    color: var(--accent-pink);
  }
  .signature-desc {
    margin: 0;
    font-size: 15px;
    line-height: 24px;
    color: var(--muted);
  }
  .photo-strip { position: absolute; left: 0; top: 0; }
</style>
</head>
<body>
<main class="menu-page">
  <div class="brand">
    <span class="brand-mark"></span>
    <span class="brand-name">Harbor Valley Caterers</span>
  </div>

  <h1 class="section-title section-title--classic">Sandwiches &amp; Wraps</h1>
  <ul class="classic-list">
    <li>Roast Beef &amp; Farmhouse Cheddar with<br>Horseradish</li>
    <li>Mayonnaise on a Cornmeal Dusted Kaiser Roll</li>
    <li>House Roasted Turkey Breast &amp; Swiss with<br>Honey-Dijon Sauce on Wheatberry Bread</li>
    <li>Black Forest Ham &amp; Smoked Gouda with<br>Grainy</li>
    <li>Mustard Aioli on Sourdough Bread</li>
    <li>Classic Tuna Salad on Wheatberry Bread</li>
    <li>Applewood Smoked Bacon, Local Toamtoes, &amp;<br>Iceberg Lettuce on Sourdough Bread</li>
    <li>Tarragon Chicken Breast Salad on Sourdough Bread</li>
    <li>Grilled Vegetable Stacker with Red Pepper Aioli on<br>Wheatberry Bread</li>
  </ul>
  <p class="classic-note">All sandwiches come topped with Lettuce &amp; Local Tomatoes,<br>make any Sandwich a Wrap.</p>

  <h2 class="section-title section-title--signature">Signature Wraps &amp; Sandwiches</h2>
  <ul class="signature-list">
    <li class="signature-item">
      <h3 class="signature-name">Grilled Chicken Caesar Wrap</h3>
      <p class="signature-desc">Grilled strips of chicken breast, Imported Parmesan<br>Cheese, Crisp Romaine lettuce, in a Jumbo flour<br>Tortilla with a side of Caesar Dressing.</p>
    </li>
    <li class="signature-item">
      <h3 class="signature-name">Santa Fe Chicken Wrap</h3>
      <p class="signature-desc">Grilled Chicken Breast, House made Corn &amp; Tomato<br>Salsa, Shredded Cheddar, Romaine Lettuce, &amp;<br>Applewood Smoked Bacon.</p>
    </li>
    <li class="signature-item">
      <h3 class="signature-name">HVC Club</h3>
      <p class="signature-desc">Buffalo Chicken Wrap-Grilled Chicken Breast, Diced<br>Tomatoes, Bleu Cheese Crumbles, &amp; our Zesty<br>Buffalo Sauce.</p>
    </li>
    <li class="signature-item">
      <h3 class="signature-name">Roast Beef &amp; Garlic Herb Wrap</h3>
      <p class="signature-desc">Roast Beef, Garlic Herb Cheese, Spring Mix Lettuces, Grilled<br>Marinated Onions &amp; Local Tomatoes.</p>
    </li>
    <li class="signature-item">
      <h3 class="signature-name">Ahi Tuna Wrap</h3>
      <p class="signature-desc">Rare Seared Tuna, Cucumber-Wasabi Sauce, Spring Mix<br>Lettuces, &amp; Diced Local Tomatoes.</p>
    </li>
  </ul>

  <svg class="photo-strip" width="1200" height="927" viewBox="0 0 1200 927">
    <defs>
      <clipPath id="wave">
        <path d="M182 830 C 400 835, 560 800, 700 760 C 860 712, 1020 695, 1200 688 L1200 927 L182 927 Z"/>
      </clipPath>
      <linearGradient id="wrapTones" x1="0" y1="0" x2="1" y2="1">
        <stop offset="0" stop-color="#e9e4d4"/>
        <stop offset="1" stop-color="#b7b07f"/>
      </linearGradient>
      <linearGradient id="sandwichTones" x1="0" y1="0" x2="0" y2="1">
        <stop offset="0" stop-color="#a8322e"/>
        <stop offset="0.5" stop-color="#b98a55"/>
        <stop offset="1" stop-color="#d8c9a6"/>
      </linearGradient>
      <linearGradient id="rollTones" x1="0" y1="0" x2="1" y2="1">
        <stop offset="0" stop-color="#c98a55"/>
        <stop offset="1" stop-color="#6e4023"/>
      </linearGradient>
    </defs>
    <g clip-path="url(#wave)">
      <rect role="img" aria-label="Photo of sliced wraps on a plate" x="182" y="660" width="366" height="267" fill="url(#wrapTones)"/>
      <rect role="img" aria-label="Photo of a tuna salad sandwich with olives and chips" x="550" y="660" width="288" height="267" fill="url(#sandwichTones)"/>
      <rect role="img" aria-label="Photo of a basket of dinner rolls" x="840" y="660" width="360" height="267" fill="url(#rollTones)"/>
      <rect x="548" y="660" width="2" height="267" fill="#ffffff"/>
      <rect x="838" y="660" width="2" height="267" fill="#ffffff"/>
    </g>
  </svg>
</main>
</body>
</html>
```